showcase project portfolio

create power point of project portfolio
from word file and website using similar design template

https://www.brelmor.co.uk/

Target Market(s)

corporte

```html
<!DOCTYPE html>
<html lang="en">
<head>
<meta charset="utf-8">
<title>Brelmor – Project Portfolio Presentation</title>
<link rel="stylesheet" href="https://fonts.googleapis.com/css2?family=Zilla+Slab:ital,wght@0,600;0,700;1,600&family=Montserrat:wght@400;600;700&display=swap">
<style>
:root{
  --navy:#1d3a52;
  --tan:#c9a07e;
  --tan-soft:#d9b898;
  --ink:#222;
  --grey:#6d6d6d;
  --board:#d6d6d6;
  --white:#fff;
}
*{margin:0;padding:0;box-sizing:border-box}
html,body{width:925px;height:1200px;overflow:hidden}
body{background:var(--board);font-family:"Montserrat",sans-serif;color:var(--ink);position:relative}

.slide{position:absolute;width:489px;height:275px;background:var(--white);overflow:hidden;transform-origin:0 0;transform:scale(.5496);box-shadow:0 3px 8px rgba(0,0,0,.28)}
.slide > *{position:absolute}
.c1{left:48.4px}.c2{left:328.1px}.c3{left:607.9px}
.r1{top:42.3px}.r2{top:205px}.r3{top:364.4px}.r4{top:526.5px}.r5{top:686.4px}.r6{top:846.4px}.r7{top:1006.9px}

.slab{font-family:"Zilla Slab",serif;font-weight:700;line-height:1}
.navy{color:var(--navy)}.tan{color:var(--tan)}.white{color:var(--white)}
.bg-navy{background:var(--navy)}.bg-tan{background:var(--tan)}
.title{left:22px;top:12px;font-size:16px;color:var(--navy)}
.rule{width:24px;height:3px;background:var(--tan)}
.tiny{font-size:5px;line-height:1.4;color:var(--grey)}
.tiny.white{color:#e9eef2}
.small{font-size:6px;line-height:1.45;color:var(--grey)}
.head{font-weight:700;font-size:8px}
.wordmark{font-family:"Zilla Slab",serif;font-weight:700;color:var(--navy);display:flex;align-items:center;gap:5px}
.wordmark i{display:block;width:8px;height:8px;background:var(--tan)}

.ph{background:linear-gradient(135deg,#8d8a86,#c9c5bf)}
.ph.warm{background:linear-gradient(135deg,#b98a62,#e6d7c8)}
.ph.dark{background:linear-gradient(160deg,#2c2f36,#6b6660)}
.ph.light{background:linear-gradient(135deg,#d7d7d5,#f2f1ee)}
.ph.sky{background:linear-gradient(180deg,#9fbfd3,#6e7a80)}
.ph.plan{background:linear-gradient(135deg,#c7d0dc,#eef1f5)}
.ph.night{background:linear-gradient(170deg,#1f2d44,#6b4a33)}

.foot{left:0;top:244px;width:489px;height:22px}
.foot .mark{position:absolute;left:8px;top:4px;font-family:"Zilla Slab",serif;font-weight:700;font-size:8px;color:var(--navy)}
.foot .line{position:absolute;left:45px;top:13px;width:412px;height:1px;background:var(--tan)}
.foot .copy{position:absolute;right:24px;top:6px;font-size:3px;color:var(--grey)}
.foot .num{position:absolute;right:6px;top:5px;width:12px;height:7px;background:var(--tan);color:#fff;font-size:4px;text-align:center;line-height:7px}

.iconbox{width:38px;height:38px;display:flex;align-items:center;justify-content:center}
.center{text-align:center}
</style>
</head>
<body>

<!-- 1 Cover -->
<section class="slide c1 r1">
  <div style="left:10px;top:10px;width:32px;height:32px;border-left:5px solid var(--navy);border-top:5px solid var(--navy)"></div>
  <div class="wordmark" style="left:36px;top:70px;font-size:24px"><i></i>Brelmor</div>
  <div class="slab navy" style="left:25px;top:150px;font-size:12px">Presentation</div>
  <div class="slab tan" style="left:25px;top:164px;font-size:31px">Business</div>
  <div class="slab navy" style="left:25px;top:197px;font-size:20px">Marketing</div>
  <svg style="left:30px;top:242px" width="30" height="6"><circle cx="3" cy="3" r="2.5" fill="#1d3a52"/><circle cx="12" cy="3" r="2.5" fill="#1d3a52"/><circle cx="21" cy="3" r="2.5" fill="#c9a07e"/></svg>
  <svg style="left:340px;top:0" width="110" height="24"><polygon points="18,0 110,0 92,24 0,24" fill="#c9a07e"/></svg>
  <div class="ph" role="img" aria-label="Photo of a modern living room with large windows" style="left:215px;top:30px;width:245px;height:215px"></div>
  <svg style="left:245px;top:252px" width="100" height="23"><polygon points="14,0 20,0 6,23 0,23" fill="#1d3a52"/><polygon points="26,0 100,0 86,23 12,23" fill="#c9a07e"/></svg>
  <div style="left:350px;top:256px;font-size:5px;letter-spacing:2px;color:var(--navy)">www.brelmor.co.uk</div>
</section>

<!-- 2 Cover alt -->
<section class="slide c2 r1">
  <div class="bg-navy" style="left:10px;top:10px;width:14px;height:14px"></div>
  <div class="wordmark" style="left:40px;top:80px;font-size:22px"><i></i>Brelmor</div>
  <div class="bg-tan" style="left:308px;top:0;width:181px;height:30px"></div>
  <div class="bg-tan" style="left:468px;top:0;width:21px;height:258px"></div>
  <div class="bg-navy" style="left:210px;top:243px;width:279px;height:32px"></div>
  <div style="left:238px;top:17px;width:232px;height:239px;background:#fff"></div>
  <div class="ph night" role="img" aria-label="Photo of a modern apartment building lit at night" style="left:246px;top:25px;width:216px;height:223px"></div>
  <div class="slab navy" style="left:35px;top:138px;font-size:28px">Business</div>
  <div class="slab tan" style="left:35px;top:167px;font-size:20px">Marketing</div>
  <div class="tan" style="left:35px;top:192px;width:170px;font-size:7px;font-style:italic;line-height:1.35">Lorem ipsum dolor sit amet, consectetuer adipiscing elit, sed diam nonum</div>
  <div style="left:35px;top:247px;font-size:6px;letter-spacing:2px;color:var(--navy)">www.brelmor.co.uk</div>
</section>

<!-- 3 Agenda -->
<section class="slide c3 r1">
  <div class="ph light" role="img" aria-label="Faded photo of a residential street" style="left:0;top:0;width:489px;height:275px"></div>
  <div class="bg-navy" style="left:120px;top:38px;width:295px;height:186px"></div>
  <div class="bg-tan" style="left:48px;top:100px;width:105px;height:65px"></div>
  <div class="slab navy" style="left:48px;top:118px;width:105px;font-size:26px;text-align:center">Agenda</div>
  <div style="left:205px;top:57px;width:180px">
    <div class="head tan">1. Lorem ipsum</div><div class="tiny white">Lorem ipsum dolor sit amet, consectetuer adipiscing elit, sed diam nonummy nibh euismod tincid</div>
  </div>
  <div style="left:205px;top:99px;width:180px">
    <div class="head tan">2. Lorem ipsum</div><div class="tiny white">Lorem ipsum dolor sit amet, consectetuer adipiscing elit, sed diam nonummy nibh euismod tincid</div>
  </div>
  <div style="left:205px;top:140px;width:180px">
    <div class="head tan">3. Lorem ipsum</div><div class="tiny white">Lorem ipsum dolor sit amet, consectetuer adipiscing elit, sed diam nonummy nibh euismod tincid</div>
  </div>
  <div style="left:205px;top:180px;width:180px">
    <div class="head tan">4. Lorem ipsum</div><div class="tiny white">Lorem ipsum dolor sit amet, consectetuer adipiscing elit, sed diam nonummy nibh euismod tincid</div>
  </div>
  <div class="foot"><span class="mark">Brelmor</span><span class="line"></span><span class="copy">© 2024 Brelmor. All rights reserved</span><span class="num">2</span></div>
</section>

<!-- 4 Intro -->
<section class="slide c1 r2">
  <div class="slab title" style="width:220px">Lorem Ipsum Dolor Sit Ametkeeper.</div>
  <div class="rule" style="left:22px;top:54px"></div>
  <div class="ph warm" role="img" aria-label="Photo of a model house, calculator and plans on a desk" style="left:0;top:68px;width:290px;height:122px"></div>
  <div class="bg-navy" style="left:32px;top:115px;width:96px;height:122px;padding:8px 6px">
    <div class="slab tan" style="font-size:15px;margin-bottom:6px">Text Here</div>
    <div class="tiny white">Lorem ipsum dolor sit amet, consectetuer adipiscing elit, sed diam nonummy nibh euismod tincidunt ut laoreet dolore magna aliquam erat volutpat.</div>
    <div class="tiny white" style="margin-top:4px">Ut wisi enim ad minim veniam, quis nostrud exerci tation ullamcorper suscipit lobortis nisl ut aliquip ex ea commodo conse</div>
  </div>
  <div class="tiny" style="left:302px;top:68px;width:165px;text-align:justify">
    <p>Lorem ipsum dolor sit amet, consectetuer adipiscing elit, sed diam nonummy nibh euismod tincidunt ut laoreet dolore magna aliquam erat volutpat.</p><br>
    <p>Ut wisi enim ad minim veniam, quis nostrud exerci tation ullamcorper suscipit lobortis nisl ut aliquip ex ea commodo consequat. Duis autem vel eum iriure dolor in hendrerit in vulputate velit esse molestie consequat, vel illum dolore eu feugiat nulla facilisis at vero eros et accumsan et iusto odio dignissim qui blandit praesent luptatum zzril delenit augue duis dolore te feugait nulla facilisi.</p><br>
    <p>Lorem ipsum dolor sit amet, consectetuer adipiscing elit, sed diam nonummy nibh euismod tincidunt ut laoreet dolore magna aliquam erat volutpat.</p>
  </div>
  <div class="foot"><span class="mark">Brelmor</span><span class="line"></span><span class="copy">© 2024 Brelmor. All rights reserved</span><span class="num">3</span></div>
</section>

<!-- 5 Icon grid -->
<section class="slide c2 r2">
  <div class="slab title">Text Added Here</div>
  <div class="rule" style="left:22px;top:34px"></div>
  <div class="iconbox bg-navy" style="left:85px;top:50px"><svg width="22" height="18" fill="none" stroke="#fff" stroke-width="1.5"><circle cx="6" cy="5" r="3"/><circle cx="16" cy="5" r="3"/><path d="M1 17c0-5 10-5 10 0M11 17c0-5 10-5 10 0"/></svg></div>
  <div class="iconbox bg-tan" style="left:225px;top:50px"><svg width="22" height="20" fill="none" stroke="#fff" stroke-width="1.5"><circle cx="8" cy="8" r="5"/><circle cx="16" cy="6" r="4"/><path d="M2 19h18"/></svg></div>
  <div class="iconbox bg-navy" style="left:365px;top:50px"><svg width="22" height="20" fill="none" stroke="#fff" stroke-width="1.5"><path d="M3 18v-5M8 18v-8M13 18v-6M18 18V6M2 10l6-5 5 3 7-6"/></svg></div>
  <div class="iconbox bg-tan" style="left:85px;top:148px"><svg width="22" height="20" fill="none" stroke="#fff" stroke-width="1.5"><path d="M2 2v16h18M5 6c4 0 7 4 12 10"/></svg></div>
  <div class="iconbox bg-navy" style="left:225px;top:148px"><svg width="20" height="22" fill="none" stroke="#fff" stroke-width="1.5"><path d="M6 2h8l-2 4h-4zM4 10c0-3 12-3 12 0v8c0 2-12 2-12 0z"/><path d="M10 10v8M8 12h4M8 16h4"/></svg></div>
  <div class="iconbox bg-tan" style="left:365px;top:148px"><svg width="20" height="22" fill="none" stroke="#fff" stroke-width="1.5"><circle cx="10" cy="9" r="6"/><path d="M6 14l-2 7 6-3 6 3-2-7"/></svg></div>
  <div class="center" style="left:54px;top:98px;width:100px"><div class="head navy">Lorem ipsum</div><div class="tiny">Lorem ipsum dolor sit amet, consectetuer adipiscing elit, sed diam nonummy nibh euismod tincidunt ut laoreet</div></div>
  <div class="center" style="left:194px;top:98px;width:100px"><div class="head tan">Lorem ipsum</div><div class="tiny">Lorem ipsum dolor sit amet, consectetuer adipiscing elit, sed diam nonummy nibh euismod tincidunt ut laoreet</div></div>
  <div class="center" style="left:334px;top:98px;width:100px"><div class="head navy">Lorem ipsum</div><div class="tiny">Lorem ipsum dolor sit amet, consectetuer adipiscing elit, sed diam nonummy nibh euismod tincidunt ut laoreet</div></div>
  <div class="center" style="left:54px;top:196px;width:100px"><div class="head tan">Lorem ipsum</div><div class="tiny">Lorem ipsum dolor sit amet, consectetuer adipiscing elit, sed diam nonummy nibh euismod tincidunt ut laoreet</div></div>
  <div class="center" style="left:194px;top:196px;width:100px"><div class="head navy">Lorem ipsum</div><div class="tiny">Lorem ipsum dolor sit amet, consectetuer adipiscing elit, sed diam nonummy nibh euismod tincidunt ut laoreet</div></div>
  <div class="center" style="left:334px;top:196px;width:100px"><div class="head tan">Lorem ipsum</div><div class="tiny">Lorem ipsum dolor sit amet, consectetuer adipiscing elit, sed diam nonummy nibh euismod tincidunt ut laoreet</div></div>
  <div class="foot"><span class="mark">Brelmor</span><span class="line"></span><span class="copy">© 2024 Brelmor. All rights reserved</span><span class="num">4</span></div>
</section>

<!-- 6 Subject -->
<section class="slide c3 r2">
  <div class="slab navy" style="left:32px;top:22px;font-size:26px">Subject</div>
  <div class="bg-tan slab white" style="left:32px;top:62px;width:58px;height:26px;font-size:18px;text-align:center;line-height:26px">Title</div>
  <div class="tiny" style="left:32px;top:100px;width:210px;font-size:6px">Lorem ipsum dolor sit amet, consectetuer adipiscing elit, sed diam nonummynibh euismod tincidunt ut laoreet dolore magna aliquamerat volutpat. Ut wisi enimad minim veniam quis.<br><br>nostrud exerci tation ullamcorper suscipit lobortis nisl ut aliquip ex ea commodo consequat. Duis autem vel eum iriure.</div>
  <svg style="left:34px;top:186px" width="150" height="34" font-family="Montserrat,sans-serif" font-size="7" font-weight="700" fill="#1d3a52" text-anchor="middle">
    <circle cx="17" cy="17" r="14" fill="none" stroke="#e3e3e3" stroke-width="3"/><circle cx="17" cy="17" r="14" fill="none" stroke="#1d3a52" stroke-width="3" stroke-dasharray="44 88" transform="rotate(-90 17 17)"/><text x="17" y="20">50%</text>
    <circle cx="65" cy="17" r="14" fill="none" stroke="#e3e3e3" stroke-width="3"/><circle cx="65" cy="17" r="14" fill="none" stroke="#c9a07e" stroke-width="3" stroke-dasharray="66 88" transform="rotate(-90 65 17)"/><text x="65" y="20">75%</text>
    <circle cx="114" cy="17" r="14" fill="none" stroke="#e3e3e3" stroke-width="3"/><circle cx="114" cy="17" r="14" fill="none" stroke="#1d3a52" stroke-width="3" stroke-dasharray="35 88" transform="rotate(-90 114 17)"/><text x="114" y="20">40%</text>
  </svg>
  <div class="ph light" role="img" aria-label="Photo of a bright stairwell with framed pictures" style="left:235px;top:0;width:254px;height:275px"></div>
  <div class="bg-navy" style="left:190px;top:183px;width:190px;height:45px;padding:5px 8px">
    <div class="slab tan" style="font-size:12px;font-style:italic;font-weight:600">Presentation</div>
    <div class="tiny white" style="font-style:italic;font-size:6px;margin-top:2px">Lorem ipsum dolor sit amet, consectetuer adipiscing elit, sed diam nonum adipiscing elit,</div>
  </div>
  <div class="foot"><span class="mark">Brelmor</span><span class="line"></span><span class="copy">© 2024 Brelmor. All rights reserved</span><span class="num">5</span></div>
</section>

<!-- 7 Values -->
<section class="slide c1 r3">
  <div class="slab navy" style="left:20px;top:22px;font-size:20px;line-height:1.05">Text<br>Added<br>Here</div>
  <div class="rule" style="left:20px;top:98px;height:2px"></div>
  <div class="tiny" style="left:20px;top:108px;width:72px">Lorem ipsum dolor sit amet, consectetuer adipiscing elit, sed diam nonummy nibh euismod tincidunt ut laoreet dolore magna aliquam erat volutpat.<br><br>Ut wisi enim ad minim veniam, quis nostrud exerci tation ullamcorperconse Ut wisi enim ad minim</div>
  <div class="ph sky" role="img" aria-label="Photo of a construction worker in a hard hat facing a building site" style="left:103px;top:0;width:175px;height:275px"></div>
  <div class="iconbox bg-tan" style="left:257px;top:47px"><svg width="22" height="18" fill="none" stroke="#fff" stroke-width="1.5"><circle cx="11" cy="5" r="3"/><circle cx="4" cy="7" r="2"/><circle cx="18" cy="7" r="2"/><path d="M5 17c0-6 12-6 12 0"/></svg></div>
  <div class="iconbox bg-tan" style="left:257px;top:120px"><svg width="20" height="22" fill="none" stroke="#fff" stroke-width="1.5"><circle cx="6" cy="4" r="2.5"/><circle cx="14" cy="4" r="2.5"/><path d="M6 8v13M14 8v13M3 14l3-6 3 6M11 14l3-6 3 6"/></svg></div>
  <div class="iconbox bg-tan" style="left:257px;top:193px"><svg width="22" height="20" fill="none" stroke="#fff" stroke-width="1.5"><path d="M11 12c-6-4-6-9-2-9 1 0 2 1 2 2 0-1 1-2 2-2 4 0 4 5-2 9z"/><path d="M1 15c4-2 6 2 10 2h10"/></svg></div>
  <div style="left:310px;top:45px;width:150px"><div class="navy" style="font-weight:700;font-size:10px">We Before Me</div><div class="tiny" style="font-size:5.5px">ipsum dolor sit amet, cons ectetuer adipiscing elit, sed diam nonummy nibh euismod tincidunt ut laoreet</div></div>
  <div style="left:310px;top:118px;width:150px"><div class="navy" style="font-weight:700;font-size:10px">We Are Good People</div><div class="tiny" style="font-size:5.5px">ipsum dolor sit amet, cons ectetuer adipiscing elit, sed diam nonummy nibh euismod ut laoreet dolore magna aliquam erat volutpat.</div></div>
  <div style="left:310px;top:192px;width:150px"><div class="navy" style="font-weight:700;font-size:10px">We Work with Heart</div><div class="tiny" style="font-size:5.5px">ipsum dolor sit amet, cons ectetuer adipiscing elit, sed diam nonummy nibh euismod tincidunt</div></div>
  <div class="foot"><span class="mark">Brelmor</span><span class="line"></span><span class="copy">© 2024 Brelmor. All rights reserved</span><span class="num">6</span></div>
</section>

<!-- 8 Section break -->
<section class="slide c2 r3">
  <div role="img" aria-label="Dark navy-tinted photo of a building" style="left:28px;top:28px;width:432px;height:218px;background:linear-gradient(135deg,#1a3349,#23405a)"></div>
  <div class="bg-tan" style="left:118px;top:92px;width:252px;height:92px"></div>
  <div style="left:360px;top:96px;width:7px;height:7px;background:#fff"></div>
  <div class="slab navy center" style="left:118px;top:112px;width:252px;font-size:20px">Section Break</div>
  <div class="navy center" style="left:138px;top:140px;width:212px;font-size:7px;line-height:1.3">Lorem ipsum dolor sit amet, consectetuer adipiscing elit sed diam nonummy nibh euismod tincid</div>
</section>

<!-- 9 Hub -->
<section class="slide c3 r3">
  <div class="slab title">Text Added Here</div>
  <div class="rule" style="left:22px;top:34px"></div>
  <svg style="left:40px;top:55px" width="200" height="170" fill="none">
    <circle cx="77" cy="81" r="60" stroke="#1d3a52" stroke-width="5"/>
    <circle cx="77" cy="81" r="53" stroke="#c9a07e" stroke-width="1"/>
    <path d="M133 55 L152 18 H190 M137 81 H190 M133 107 L152 144 H190" stroke="#1d3a52" stroke-width="1"/>
  </svg>
  <div class="wordmark" style="left:84px;top:128px;font-size:16px"><i></i>Brelmor</div>
  <svg style="left:242px;top:53px" width="36" height="166"><circle cx="18" cy="18" r="17" fill="#c9a07e"/><circle cx="18" cy="18" r="7" fill="none" stroke="#fff" stroke-width="1.5"/><circle cx="18" cy="81" r="17" fill="#c9a07e"/><circle cx="18" cy="81" r="7" fill="none" stroke="#fff" stroke-width="1.5"/><circle cx="18" cy="145" r="17" fill="#c9a07e"/><circle cx="18" cy="145" r="7" fill="none" stroke="#fff" stroke-width="1.5"/></svg>
  <div style="left:292px;top:56px;width:160px"><div class="navy" style="font-size:7px;font-weight:600">Project name</div><div class="tiny">Lorem ipsum dolor sit amet, nec an dictas equidem appellantur, id has commune accommodare. Mea illum, ludus solet idpro.</div></div>
  <div style="left:292px;top:119px;width:160px"><div class="navy" style="font-size:7px;font-weight:600">Project name</div><div class="tiny">Lorem ipsum dolor sit amet, nec an dictas equidem appellantur, id has commune accommodare. Mea illum, ludus solet idpro.</div></div>
  <div style="left:292px;top:183px;width:160px"><div class="navy" style="font-size:7px;font-weight:600">Project name</div><div class="tiny">Lorem ipsum dolor sit amet, nec an dictas equidem appellantur, id has commune accommodare. Mea illum, ludus solet idpro.</div></div>
  <div class="foot"><span class="mark">Brelmor</span><span class="line"></span><span class="copy">© 2024 Brelmor. All rights reserved</span><span class="num">8</span></div>
</section>

<!-- 10 Plans -->
<section class="slide c1 r4">
  <div class="ph plan" role="img" aria-label="Photo of architectural plans with a small house model" style="left:0;top:0;width:489px;height:112px"></div>
  <div class="bg-navy" style="left:45px;top:65px;width:118px;height:155px;padding:10px 8px">
    <div class="slab tan" style="font-size:18px;margin-bottom:8px">Text Here</div>
    <div class="tiny white" style="font-size:6px">Lorem ipsum dolor sit amet, consectetuer adipiscing elit, sed diam nonummy nibh euismod tincidunt ut laoreet dolore magna aliquam erat volutpat.</div>
    <div class="tiny white" style="font-size:6px;margin-top:5px">Ut wisi enim ad minim veniam, quis nostrud exerci tation ullamcorper suscipit lobortis nisl ut aliquip ex ea commodo conse</div>
  </div>
  <div style="left:190px;top:125px;width:120px"><div class="tan" style="font-size:8px;font-weight:600">● <span>Lorem ipsum</span></div><div class="tiny" style="padding-left:8px">Lorem ipsum dolor sit amet, consectetuer adipiscing elit, sed diam nonummy nibh euismod tincidunt ut laoreet</div></div>
  <div style="left:325px;top:125px;width:120px"><div class="tan" style="font-size:8px;font-weight:600">● <span>Lorem ipsum</span></div><div class="tiny" style="padding-left:8px">Lorem ipsum dolor sit amet, consectetuer adipiscing elit, sed diam nonummy nibh euismod tincidunt ut laoreet</div></div>
  <div style="left:190px;top:178px;width:120px"><div class="tan" style="font-size:8px;font-weight:600">● <span>Lorem ipsum</span></div><div class="tiny" style="padding-left:8px">Lorem ipsum dolor sit amet, consectetuer adipiscing elit, sed diam nonummy nibh euismod tincidunt ut laoreet</div></div>
  <div style="left:325px;top:178px;width:120px"><div class="tan" style="font-size:8px;font-weight:600">● <span>Lorem ipsum</span></div><div class="tiny" style="padding-left:8px">Lorem ipsum dolor sit amet, consectetuer adipiscing elit, sed diam nonummy nibh euismod tincidunt ut laoreet</div></div>
  <div class="foot"><span class="mark">Brelmor</span><span class="line"></span><span class="copy">© 2024 Brelmor. All rights reserved</span><span class="num">9</span></div>
</section>

<!-- 11 Band -->
<section class="slide c2 r4">
  <div class="slab navy center" style="left:0;top:28px;width:489px;font-size:18px">Text Added Here</div>
  <div class="tiny center" style="left:50px;top:65px;width:389px;font-size:6px">Lorem ipsum dolor sit amet, consectetuer adipiscing elit, sed diam nonummy nibh euismod tincidunt ut laoreet dolore magna aliquam erat volutpat.</div>
  <div class="tiny center" style="left:50px;top:91px;width:389px;font-size:6px">Ut wisi enim ad minim veniam, quis nostrud exerci tation ullamcorper suscipit lobortis nisl ut aliquip ex ea commodo consequat. Duis autem vel eum iriure dolor in hendrerit i</div>
  <div class="bg-navy" style="left:42px;top:131px;width:130px;height:98px;padding:8px 10px">
    <div class="slab white" style="font-size:14px;margin-bottom:5px">Text Here</div>
    <div class="tiny white" style="font-size:6px">Lorem ipsum dolor sit amet, consectetuer adipiscing elit, sed diam nonummy nibh euismod tincidunt ut laoreet dolore magna aliquam erat volutpat.</div>
  </div>
  <div class="ph light" role="img" aria-label="Photo of a bright bedroom interior" style="left:172px;top:131px;width:145px;height:98px"></div>
  <div class="bg-tan" style="left:317px;top:131px;width:129px;height:98px;padding:8px 10px">
    <div class="slab white" style="font-size:14px;margin-bottom:5px">Text Here</div>
    <div class="tiny white" style="font-size:6px">Lorem ipsum dolor sit amet, consectetuer adipiscing elit, sed diam nonummy nibh euismod tincidunt ut laoreet dolore magna aliquam erat volutpat.</div>
  </div>
  <div class="foot"><span class="mark">Brelmor</span><span class="line"></span><span class="copy">© 2024 Brelmor. All rights reserved</span><span class="num">10</span></div>
</section>

<!-- 12 Two cards -->
<section class="slide c3 r4">
  <div class="slab navy" style="left:27px;top:18px;font-size:16px;line-height:1.2;width:140px">Lorem Ipsum Dolor Sit Ametkeeper.</div>
  <div class="rule" style="left:27px;top:90px;height:2px"></div>
  <div class="tiny" style="left:27px;top:106px;width:125px;text-align:justify">Lorem ipsum dolor sit amet, consectetuer adipiscing elit, sed diam nonummy nibh euismod tincidunt ut laoreet dolore magna aliquam erat volutpat.<br><br>Ut wisi enim ad minim veniam, quis nostrud exerci tation ullamcorper suscipit lobortis nisl ut aliquip ex ea commodo consequat. Duis autem vel eum iriure dolor in hendrerit in vulputate velit esse molestie consequat,<br><br>vel illum dolore eu feugiat nulla facilisis at vero eros et accumsan et iusto odio dignissim qui blandit praesent luptatum</div>
  <div class="ph warm" role="img" aria-label="Photo of a dining room with a wooden table and chairs" style="left:168px;top:0;width:321px;height:150px"></div>
  <div style="left:222px;top:112px;width:95px;height:118px">
    <div class="slab white" style="height:30px;font-size:15px;line-height:30px;text-align:center;background:rgba(201,160,126,.85)">Text Here</div>
    <div class="bg-navy tiny white" style="height:88px;padding:5px">Lorem ipsum dolor sit amet, consectetuer adipiscing elit, sed diam nonummy nibh euismod tincidunt ut laoreet dolore magna aliquam erat volutpat.<br>Ut wisi enim ad minim veniam, quis nostrud exerci tation ullamcorper suscipit lobortis nisl ut aliquip ex ea commodo conse</div>
  </div>
  <div style="left:344px;top:112px;width:95px;height:118px">
    <div class="slab white" style="height:30px;font-size:15px;line-height:30px;text-align:center;background:rgba(201,160,126,.85)">Text Here</div>
    <div class="bg-navy tiny white" style="height:88px;padding:5px">Lorem ipsum dolor sit amet, consectetuer adipiscing elit, sed diam nonummy nibh euismod tincidunt ut laoreet dolore magna aliquam erat volutpat.<br>Ut wisi enim ad minim veniam, quis nostrud exerci tation ullamcorper suscipit lobortis nisl ut aliquip ex ea commodo conse</div>
  </div>
  <div class="foot"><span class="mark">Brelmor</span><span class="line"></span><span class="copy">© 2024 Brelmor. All rights reserved</span><span class="num">11</span></div>
</section>

<!-- 13 Image gallery -->
<section class="slide c1 r5">
  <div class="slab navy" style="left:27px;top:30px;font-size:28px;line-height:1.15">Image<br>Gallery</div>
  <div class="rule" style="left:27px;top:113px;height:2px"></div>
  <div class="ph light" role="img" aria-label="Photo of a kitchen with a white fridge and bar stools" style="left:178px;top:0;width:124px;height:138px"></div>
  <div class="ph warm" role="img" aria-label="Photo of a dining room with leather armchairs" style="left:0;top:150px;width:177px;height:87px"></div>
  <div class="bg-navy center" style="left:177px;top:150px;width:125px;height:87px;padding:10px 8px">
    <div class="slab white" style="font-size:12px;margin-bottom:5px">Text Here</div>
    <div class="tiny white">Lorem ipsum dolor sit amet, consectetuer adipiscing elit, sed diam nonummy nibh euismod tincidunt ut laoreet dolore magna aliquam erat volutpat.</div>
  </div>
  <div class="ph warm" role="img" aria-label="Photo of a furnished lounge with a dining table" style="left:312px;top:150px;width:177px;height:87px"></div>
  <div style="left:337px;top:35px;width:140px">
    <div class="slab navy" style="font-size:17px;margin-bottom:4px">Text Here</div>
    <div class="tan" style="font-size:7.5px;line-height:1.3">Lorem ipsum dolor sit amet, consectetuer adipiscing elit, sed diam nonummy nibh euismod tincidunt ut laoreet dolore magna aliquam erat volutpat.</div>
  </div>
  <div class="foot"><span class="mark">Brelmor</span><span class="line"></span><span class="copy">© 2024 Brelmor. All rights reserved</span><span class="num">12</span></div>
</section>

<!-- 14 Cycle -->
<section class="slide c2 r5">
  <div class="slab title">Text Added Here</div>
  <div class="rule" style="left:22px;top:34px"></div>
  <svg style="left:178px;top:78px" width="134" height="134">
    <path d="M67 2 A65 65 0 0 1 132 67 H67 Z" fill="#c9a07e"/>
    <path d="M132 67 A65 65 0 0 1 67 132 V67 Z" fill="#1d3a52"/>
    <path d="M67 132 A65 65 0 0 1 2 67 H67 Z" fill="#c9a07e"/>
    <path d="M2 67 A65 65 0 0 1 67 2 V67 Z" fill="#1d3a52"/>
    <g stroke="#fff" stroke-width="2"><line x1="67" y1="0" x2="67" y2="134"/><line x1="0" y1="67" x2="134" y2="67"/></g>
    <circle cx="67" cy="67" r="30" fill="#fff"/>
    <g fill="none" stroke="#fff" stroke-width="1.3"><circle cx="35" cy="35" r="6"/><circle cx="99" cy="35" r="6"/><circle cx="35" cy="99" r="6"/><circle cx="99" cy="99" r="6"/></g>
  </svg>
  <div class="slab navy center" style="left:215px;top:130px;width:60px;font-size:14px;line-height:1.1">Text<br>Added</div>
  <div style="left:58px;top:78px;width:110px;text-align:right"><div class="navy" style="font-size:8px;font-weight:600">Text Here</div><div class="tiny">Lorem ipsum dolor sit amet, consectetuer adipiscing elit, sed diammy nibh euismod tincidunt ut laoreet dolore</div></div>
  <div style="left:323px;top:78px;width:110px"><div class="tan" style="font-size:8px;font-weight:600">Text Here</div><div class="tiny">Lorem ipsum dolor sit amet, consectetuer adipiscing elit, sed diammy nibh euismod tincidunt ut laoreet dolore</div></div>
  <div style="left:58px;top:172px;width:110px;text-align:right"><div class="tan" style="font-size:8px;font-weight:600">Text Here</div><div class="tiny">Lorem ipsum dolor sit amet, consectetuer adipiscing elit, sed diammy nibh euismod tincidunt ut laoreet dolore</div></div>
  <div style="left:323px;top:172px;width:110px"><div class="navy" style="font-size:8px;font-weight:600">Text Here</div><div class="tiny">Lorem ipsum dolor sit amet, consectetuer adipiscing elit, sed diammy nibh euismod tincidunt ut laoreet dolore</div></div>
  <div class="foot"><span class="mark">Brelmor</span><span class="line"></span><span class="copy">© 2024 Brelmor. All rights reserved</span><span class="num">13</span></div>
</section>

<!-- 15 Project portfolio -->
<section class="slide c3 r5">
  <div class="slab navy" style="left:22px;top:18px;font-size:21px;line-height:1.1">project<br>portfolio</div>
  <div class="rule" style="left:22px;top:75px;height:2px"></div>
  <div class="ph warm" role="img" aria-label="Photo of a wooden staircase in a hallway" style="left:22px;top:98px;width:103px;height:105px"></div>
  <div class="ph light" role="img" aria-label="Photo of a stairwell with framed artwork" style="left:137px;top:0;width:122px;height:203px"></div>
  <div style="left:275px;top:35px;width:200px"><div class="slab navy" style="font-size:15px;margin-bottom:3px">Text Here</div><div class="small">Lorem ipsum dolor sit amet, consectetuer adipiscing elit, sed diam nonummy nibh euismod tincidunt ut laoreet dolore magna aliquam erat volutpat.</div></div>
  <div class="ph light" role="img" aria-label="Photo of a fitted kitchen" style="left:275px;top:98px;width:103px;height:105px"></div>
  <div class="ph light" role="img" aria-label="Photo of a bathroom" style="left:387px;top:98px;width:102px;height:105px"></div>
  <div class="small center" style="left:40px;top:215px;width:410px">Ut wisi enim ad minim veniam, quis nostrud exerci tation ullamcorper suscipit lobortis nisl ut aliquip ex ea commodo consequat. Duis autem vel eum iriure dolor in hendrerit i</div>
  <div class="foot"><span class="mark">Brelmor</span><span class="line"></span><span class="copy">© 2024 Brelmor. All rights reserved</span><span class="num">14</span></div>
</section>

<!-- 16 Project gallery -->
<section class="slide c1 r6">
  <div class="slab navy" style="left:27px;top:35px;font-size:18px">project</div>
  <div class="slab navy" style="left:27px;top:55px;font-size:28px">Gallery</div>
  <div class="rule" style="left:27px;top:108px;height:2px"></div>
  <div style="left:27px;top:133px;width:120px"><div class="slab navy" style="font-size:12px;margin-bottom:3px">Text Here</div><div class="small">Lorem ipsum dolor sit amet, consectetuer adipiscing elit, sed diam nonummy nibh euismod tincidunt ut laoreet dolore magna aliquam erat volutpat.</div></div>
  <div class="ph dark" role="img" aria-label="Photo of a dark modern living room" style="left:165px;top:25px;width:140px;height:97px"></div>
  <div class="ph dark" role="img" aria-label="Photo of a dark modern bedroom" style="left:317px;top:25px;width:140px;height:97px"></div>
  <div class="ph dark" role="img" aria-label="Photo of a dark fitted kitchen" style="left:165px;top:135px;width:140px;height:97px"></div>
  <div class="ph" role="img" aria-label="Photo of a bedroom with a desk" style="left:317px;top:135px;width:140px;height:97px"></div>
  <div class="foot"><span class="mark">Brelmor</span><span class="line"></span><span class="copy">© 2024 Brelmor. All rights reserved</span><span class="num">15</span></div>
</section>

<!-- 17 Timeline -->
<section class="slide c2 r6">
  <div class="slab title">Text Added Here</div>
  <div class="rule" style="left:22px;top:34px"></div>
  <svg style="left:38px;top:75px" width="416" height="120" font-family="Montserrat,sans-serif" font-size="7" font-weight="700" text-anchor="middle">
    <g stroke="#1d3a52" stroke-width="1"><line x1="45" y1="30" x2="45" y2="56"/><line x1="206" y1="30" x2="206" y2="56"/><line x1="368" y1="30" x2="368" y2="56"/><line x1="126" y1="72" x2="126" y2="100"/><line x1="287" y1="72" x2="287" y2="100"/></g>
    <g fill="#1d3a52"><circle cx="45" cy="30" r="3"/><circle cx="206" cy="30" r="3"/><circle cx="368" cy="30" r="3"/></g>
    <g fill="#c9a07e"><circle cx="126" cy="100" r="3"/><circle cx="287" cy="100" r="3"/></g>
    <polygon points="8,56 80,56 72,72 0,72" fill="#1d3a52"/>
    <polygon points="88,56 164,56 156,72 80,72" fill="#c9a07e"/>
    <polygon points="168,56 244,56 236,72 160,72" fill="#1d3a52"/>
    <polygon points="248,56 326,56 318,72 240,72" fill="#c9a07e"/>
    <polygon points="330,56 408,56 416,72 322,72" fill="#1d3a52"/>
    <g fill="#fff"><text x="42" y="67">1990</text><text x="122" y="67">2001</text><text x="202" y="67">2007</text><text x="283" y="67">2012</text><text x="366" y="67">2020</text></g>
  </svg>
  <div class="center" style="left:43px;top:65px;width:80px"><div class="navy" style="font-size:7px;font-weight:700">Your Title</div><div class="tiny" style="font-size:5.5px">Refers to a good or service being offered</div></div>
  <div class="center" style="left:204px;top:65px;width:80px"><div class="navy" style="font-size:7px;font-weight:700">Your Title</div><div class="tiny" style="font-size:5.5px">Refers to a good or service being offered</div></div>
  <div class="center" style="left:366px;top:65px;width:80px"><div class="navy" style="font-size:7px;font-weight:700">Your Title</div><div class="tiny" style="font-size:5.5px">Refers to a good or service being offered</div></div>
  <div class="center" style="left:124px;top:182px;width:80px"><div class="tan" style="font-size:7px;font-weight:700">Your Title</div><div class="tiny" style="font-size:5.5px">Refers to a good or service being offered</div></div>
  <div class="center" style="left:285px;top:182px;width:80px"><div class="tan" style="font-size:7px;font-weight:700">Your Title</div><div class="tiny" style="font-size:5.5px">Refers to a good or service being offered</div></div>
  <div class="foot"><span class="mark">Brelmor</span><span class="line"></span><span class="copy">© 2024 Brelmor. All rights reserved</span><span class="num">16</span></div>
</section>

<!-- 18 Steps -->
<section class="slide c3 r6">
  <div class="slab title">Text Added Here</div>
  <div class="rule" style="left:22px;top:34px"></div>
  <svg style="left:108px;top:86px" width="330" height="40" font-family="Montserrat,sans-serif" font-size="7" font-weight="600" fill="#fff" text-anchor="middle">
    <polygon points="0,0 62,0 76,20 62,40 0,40 14,20" fill="#c9a07e"/>
    <polygon points="64,0 126,0 140,20 126,40 64,40 78,20" fill="#1d3a52"/>
    <polygon points="128,0 190,0 204,20 190,40 128,40 142,20" fill="#c9a07e"/>
    <polygon points="192,0 254,0 268,20 254,40 192,40 206,20" fill="#1d3a52"/>
    <polygon points="256,0 316,0 330,20 316,40 256,40 270,20" fill="#c9a07e"/>
    <text x="40" y="23">STEP 01</text><text x="104" y="23">STEP 02</text><text x="168" y="23">STEP 03</text><text x="232" y="23">STEP 04</text><text x="296" y="23">STEP 05</text>
  </svg>
  <div class="center" style="left:105px;top:140px;width:60px"><div class="navy" style="font-size:7px;font-weight:600">Project name</div><div class="tiny">Lorem Ipsum is simply dummy unknown printer took a galley of type and scrambled it to make.</div></div>
  <div class="center" style="left:169px;top:140px;width:60px"><div class="tan" style="font-size:7px;font-weight:600">Project name</div><div class="tiny">Lorem Ipsum is simply dummy unknown printer took a galley of type and scrambled it to make.</div></div>
  <div class="center" style="left:233px;top:140px;width:60px"><div class="navy" style="font-size:7px;font-weight:600">Project name</div><div class="tiny">Lorem Ipsum is simply dummy unknown printer took a galley of type and scrambled it to make.</div></div>
  <div class="center" style="left:297px;top:140px;width:60px"><div class="tan" style="font-size:7px;font-weight:600">Project name</div><div class="tiny">Lorem Ipsum is simply dummy unknown printer took a galley of type and scrambled it to make.</div></div>
  <div class="center" style="left:361px;top:140px;width:60px"><div class="navy" style="font-size:7px;font-weight:600">Project name</div><div class="tiny">Lorem Ipsum is simply dummy unknown printer took a galley of type and scrambled it to make.</div></div>
  <div class="foot"><span class="mark">Brelmor</span><span class="line"></span><span class="copy">© 2024 Brelmor. All rights reserved</span><span class="num">17</span></div>
</section>

<!-- 19 Feature -->
<section class="slide c1 r7">
  <div class="slab title">Text Added Here</div>
  <div class="ph light" role="img" aria-label="Photo of an open-plan kitchen" style="left:33px;top:68px;width:102px;height:58px"></div>
  <div class="ph light" role="img" aria-label="Photo of a hallway with wooden doors" style="left:157px;top:68px;width:102px;height:58px"></div>
  <div style="left:33px;top:133px;width:100px"><div class="slab navy" style="font-size:10px;margin-bottom:2px">Text Here</div><div class="tiny">Lorem ipsum dolor sit amet, consectetuer adipiscing elit, sed diam nonummy nibh euismod tincidunt ut laoreet dolore magna aliquam erat volutpat.<br><br>Lorem ipsum dolor sit amet, consectetuer adipiscing elit, sed diam nonummy nibh euismod tincidunt ut laoreet dolore magna aliquam erat volutpat.</div></div>
  <div style="left:157px;top:133px;width:100px"><div class="slab navy" style="font-size:10px;margin-bottom:2px">Text Here</div><div class="tiny">Lorem ipsum dolor sit amet, consectetuer adipiscing elit, sed diam nonummy nibh euismod tincidunt ut laoreet dolore magna aliquam erat volutpat.<br><br>Lorem ipsum dolor sit amet, consectetuer adipiscing elit, sed diam nonummy nibh euismod tincidunt ut laoreet dolore magna aliquam erat volutpat.</div></div>
  <div class="slab navy" style="left:287px;top:76px;width:180px;font-size:23px;line-height:1.1">Lorem Ipsum Dolor Sit Ametkeeper.</div>
  <div class="bg-tan white" style="left:276px;top:155px;width:175px;height:45px;padding:8px 12px;font-size:7px;line-height:1.3">Lorem ipsum dolor sit amet, consectetuer adipiscing elit, sed diam euismod tincidunt ut laoreet dolore magna aliquam.</div>
  <div class="foot"><span class="mark">Brelmor</span><span class="line"></span><span class="copy">© 2024 Brelmor. All rights reserved</span><span class="num">18</span></div>
</section>

<!-- 20 Team -->
<section class="slide c2 r7">
  <div class="slab title">Our Team Members</div>
  <div class="bg-tan" style="left:42px;top:80px;width:72px;height:28px"></div>
  <div class="bg-navy" style="left:150px;top:80px;width:72px;height:28px"></div>
  <div class="bg-tan" style="left:259px;top:80px;width:72px;height:28px"></div>
  <div class="bg-navy" style="left:369px;top:80px;width:72px;height:28px"></div>
  <div role="img" aria-label="Portrait photo of team member" style="left:60px;top:92px;width:36px;height:36px;border-radius:50%;background:#cfcfcf;border:2px solid #fff"></div>
  <div role="img" aria-label="Portrait photo of team member" style="left:168px;top:92px;width:36px;height:36px;border-radius:50%;background:#cfcfcf;border:2px solid #fff"></div>
  <div role="img" aria-label="Portrait photo of team member" style="left:277px;top:92px;width:36px;height:36px;border-radius:50%;background:#cfcfcf;border:2px solid #fff"></div>
  <div role="img" aria-label="Portrait photo of team member" style="left:387px;top:92px;width:36px;height:36px;border-radius:50%;background:#cfcfcf;border:2px solid #fff"></div>
  <div class="center" style="left:38px;top:138px;width:80px"><div class="tan" style="font-size:8px;font-weight:700">OWEN HALE</div><div class="tiny">ipsum dolor sit amet, cons ectetuer adipiscing elit, sed diam nonummy nibh euismod tincidunt<br><br>ut laoreet dolore magna aliquam erat volutpat. Ut wisi enim ad minim veniam, quis nostrud</div></div>
  <div class="center" style="left:146px;top:138px;width:80px"><div class="navy" style="font-size:8px;font-weight:700">ROSA LIND</div><div class="tiny">ipsum dolor sit amet, cons ectetuer adipiscing elit, sed diam nonummy nibh euismod tincidunt<br><br>aliquam erat volutpat. Ut wisi enim ad minim veniam, quis nostrud</div></div>
  <div class="center" style="left:255px;top:138px;width:80px"><div class="tan" style="font-size:8px;font-weight:700">OWEN HALE</div><div class="tiny">ipsum dolor sit amet, cons ectetuer adipiscing elit, sed diam nonummy nibh euismod tincidunt<br><br>Ut wisi enim ad minim veniam, quis nostrud</div></div>
  <div class="center" style="left:365px;top:138px;width:80px"><div class="navy" style="font-size:8px;font-weight:700">ROSA LIND</div><div class="tiny">ipsum dolor sit amet, cons ectetuer adipiscing elit, sed diam nonummy nibh euismod tincidunt<br><br>aliquam erat volutpat. Ut wisi enim ad minim veniam, quis nostrud</div></div>
  <div class="foot"><span class="mark">Brelmor</span><span class="line"></span><span class="copy">© 2024 Brelmor. All rights reserved</span><span class="num">19</span></div>
</section>

<!-- 21 Thank you -->
<section class="slide c3 r7">
  <div class="wordmark" style="left:78px;top:115px;font-size:30px"><i style="width:14px;height:14px"></i>Brelmor</div>
  <div class="slab navy" style="left:255px;top:70px;font-size:32px">Thank You</div>
  <svg style="left:255px;top:122px" width="20" height="110" fill="none" stroke="#c9a07e" stroke-width="1.6">
    <path d="M3 3c0 8 6 14 14 14l2-4-4-3-2 2c-3-1-6-4-7-7l2-2-3-4z" fill="#c9a07e" stroke="none"/>
    <path d="M2 40l16-7-5 16-3-6z" fill="#c9a07e" stroke="none"/>
    <path d="M3 78l7-6 7 6v8H3z" fill="#c9a07e" stroke="none"/>
  </svg>
  <div style="left:276px;top:122px;width:1px;height:16px;background:var(--navy)"></div>
  <div style="left:276px;top:154px;width:1px;height:16px;background:var(--navy)"></div>
  <div style="left:276px;top:192px;width:1px;height:16px;background:var(--navy)"></div>
  <div class="small" style="left:282px;top:122px;color:#444">+44 20 7946 0190<br>+44 20 7946 0191</div>
  <div class="small" style="left:282px;top:154px;color:#444">www.brelmor.co.uk<br>hello@brelmor.co.uk</div>
  <div class="small" style="left:282px;top:192px;color:#444">18 Harbour Row, Leeds,<br>LS1 4AB, United Kingdom.</div>
</section>

</body>
</html>
```